Small Business Broker Business Card Design

A business card design for a small business brokerage, which is a financial service, not unlike real estate brokerage, but for small businesses such as laundromats, pizza shops, restaurants, cleaners etc. The designs should all be simple, more conservative in nature, using the colors and font of the logo. Again, think real estate Brokerage as a business context
Contact Information for Business Card
Name: Glen R. Harlow. Title: Small Business Advisor. Email: g.harlow@bayfieldcapitalworks.example. Mobile: (555) 274-3918. Office: (555) 806-2147. www.bayfieldcapitalworks.example

```html
<!DOCTYPE html>
<html lang="en">
<head>
<meta charset="utf-8">
<title>Bayfield Capital Works – Business Card</title>
<link href="https://fonts.googleapis.com/css2?family=Montserrat:wght@400;500;600;700&display=swap" rel="stylesheet">
<style>
  :root {
    --navy: #1c3a6b;
    --navy-light: #2f5190;
    --green: #8dc63f;
    --white: #ffffff;
    --ink: #1e2233;
    --backdrop: #9a9a9a;
  }
  * { margin: 0; padding: 0; box-sizing: border-box; }
  html, body { width: 1093px; height: 1200px; overflow: hidden; }
  body {
    background: var(--backdrop);
    font-family: "Montserrat", sans-serif;
    position: relative;
  }
  .card {
    position: absolute;
    left: 265px;
    width: 580px;
    height: 363px;
    border-radius: 15px;
    overflow: hidden;
  }
  .card--front { top: 225px; background: var(--white); }
  .card--back  { top: 615px; height: 366px; }

  /* Front */
  .front-wave { position: absolute; left: 0; top: 0; width: 580px; height: 363px; }
  .brand {
    position: absolute;
    left: 0; width: 282px;
    top: 155px;
    text-align: center;
  }
  .brand__mark {
    width: 34px; height: 34px;
    background: var(--navy);
    margin: 0 auto 12px;
  }
  .brand__name {
    color: var(--navy);
    font-weight: 700;
    font-size: 12.5px;
    letter-spacing: 0.1px;
  }
  .brand__tagline {
    color: var(--green);
    font-weight: 600;
    font-size: 6.4px;
    letter-spacing: 0.9px;
    margin-top: 3px;
    text-transform: uppercase;
  }
  .divider {
    position: absolute;
    left: 271px; top: 116px;
    width: 1.5px; height: 149px;
    background: var(--navy);
  }
  .person {
    position: absolute;
    left: 282px; top: 112px;
  }
  .person__name {
    color: var(--navy);
    font-weight: 700;
    font-size: 22.5px;
    line-height: 1.1;
  }
  .person__title {
    color: var(--ink);
    font-weight: 500;
    font-size: 13px;
    margin-top: 1px;
  }
  .contacts {
    position: absolute;
    left: 283px; top: 185px;
    list-style: none;
  }
  .contacts li {
    display: flex;
    align-items: center;
    height: 19.5px;
    color: var(--ink);
    font-size: 12.6px;
    font-weight: 400;
    white-space: nowrap;
  }
  .contacts li.contact--email { font-size: 11.6px; }
  .contacts svg { width: 13px; height: 13px; margin-right: 9px; flex: none; fill: var(--navy); }

  /* Back */
  .back-field {
    position: absolute; inset: 0;
    background: radial-gradient(ellipse 300px 220px at 100% 0%, var(--navy-light), rgba(47,81,144,0) 100%), var(--navy);
  }
  .back-brand {
    position: absolute;
    left: 0; right: 0; top: 205px;
    text-align: center;
  }
  .back-brand__mark {
    width: 40px; height: 40px;
    background: var(--green);
    margin: 0 auto 20px;
  }
  .back-brand__name {
    color: var(--white);
    font-weight: 700;
    font-size: 18px;
    letter-spacing: 0.3px;
  }
  .back-brand__tagline {
    color: var(--green);
    font-weight: 600;
    font-size: 9.6px;
    letter-spacing: 1.5px;
    margin-top: 3px;
    text-transform: uppercase;
  }
</style>
</head>
<body>

<section class="card card--front">
  <svg class="front-wave" viewBox="0 0 580 363" aria-hidden="true">
    <path d="M0 281 Q250 338 530 302 Q250 330 0 292 Z" fill="var(--green)"/>
    <path d="M0 296 Q290 346 580 296 L580 363 L0 363 Z" fill="var(--navy)" stroke="var(--white)" stroke-width="2"/>
  </svg>

  <div class="brand">
    <div class="brand__mark"></div>
    <div class="brand__name">BAYFIELD CAPITAL WORKS, INC</div>
    <div class="brand__tagline">Confidently buy or sell a local business today</div>
  </div>

  <div class="divider"></div>

  <div class="person">
    <div class="person__name">Glen R. Harlow</div>
    <div class="person__title">Small Business Advisor</div>
  </div>

  <ul class="contacts">
    <li>
      <svg viewBox="0 0 24 24"><path d="M3 9c0-3 4-5 9-5s9 2 9 5v2h-5V8.5c-1-.5-2.5-.8-4-.8s-3 .3-4 .8V11H3zM6 12h12l2 8H4zm6 2a2.5 2.5 0 100 5 2.5 2.5 0 000-5z"/></svg>
      (555) 806-2147
    </li>
    <li>
      <svg viewBox="0 0 24 24"><path d="M6.6 10.8a15 15 0 006.6 6.6l2.2-2.2c.3-.3.7-.4 1-.2 1.1.4 2.3.6 3.6.6.6 0 1 .4 1 1V20c0 .6-.4 1-1 1A17 17 0 013 4c0-.6.4-1 1-1h3.5c.6 0 1 .4 1 1 0 1.3.2 2.5.6 3.6.1.3 0 .7-.2 1z"/></svg>
      (555) 274-3918
    </li>
    <li class="contact--email">
      <svg viewBox="0 0 24 24"><path d="M2 5h20v2l-10 6L2 7zm0 4.3l10 6 10-6V19H2z"/></svg>
      g.harlow@bayfieldcapitalworks.example
    </li>
    <li>
      <svg viewBox="0 0 24 24"><path d="M12 2a10 10 0 100 20 10 10 0 000-20zm-1 17.9A8 8 0 014.2 9.2L9 14v1a2 2 0 002 2zm6.9-2.5A2 2 0 0016 16h-1v-3a1 1 0 00-1-1H8v-2h2a1 1 0 001-1V7h2a2 2 0 002-2v-.4a8 8 0 012.9 12.8z"/></svg>
      www.bayfieldcapitalworks.example
    </li>
  </ul>
</section>

<section class="card card--back">
  <div class="back-field" role="img" aria-label="Navy background with a faint repeating brand pattern, brightening toward the top right"></div>
  <div class="back-brand">
    <div class="back-brand__mark"></div>
    <div class="back-brand__name">BAYFIELD CAPITAL WORKS, INC</div>
    <div class="back-brand__tagline">Confidently buy or sell a local business today</div>
  </div>
</section>

</body>
</html>
```